Business card

We need a business card design for our company based in Auckland , New Zealand called 'Ridge + Studio Ltd'. We provide architectural services. We would like to see designs that use the max. three colours (such as white, black, grey) The final design should communicate financial safety and growth."
Also I will provide our company logo. I would like to the logo to be embeded onto our business card.

Target Market(s)

new residential house, alteration & addition & light commericila design & drafting service

Industry/Entity Type

Architecture

Contact Information for Business Card

Company name: ridge + studio Ltd.
Name: Mark Delford
Job title: architectural designer & Design LBP
email address: mark@rplusd.co.nz
mobile number: 02 5163 2290
web site: www.rplusd.co.nz

Requirements
Must have
• My project must have..
• - embeded logo (attached company logo)
• I don't have a bigger version for our company logo, but I have one old one, so you can remove the word from it)
• - insert the attached small BKTW logo & LBP logo
• - creative, simple and clear business card.
• - Max. three colours
Nice to have
• - Here are the samples I would like to share with you: http://www.plimvora.com/blog/minimalistic-business-card-designs/
• I would like to have my business card like one of the creation.
Should not have
• TBA

```html
<!DOCTYPE html>
<html lang="en">
<head>
<meta charset="utf-8">
<title>Ridge + Studio Ltd — Business Card</title>
<link rel="stylesheet" href="https://fonts.googleapis.com/css2?family=Open+Sans:wght@400;600&display=swap">
<style>
  :root {
    --stage-top: #2e2e2e;
    --stage-bottom: #050505;
    --card-front: #f2f2f2;
    --card-back: #ffffff;
    --ink: #111111;
    --ink-soft: #222222;
    --badge-grey: #9a9a9a;
  }
  html, body {
    margin: 0;
    padding: 0;
    width: 1200px;
    height: 900px;
    overflow: hidden;
  }
  body {
    position: relative;
    background: linear-gradient(180deg, var(--stage-top) 0%, #1a1a1a 45%, var(--stage-bottom) 100%);
    font-family: "Open Sans", Arial, sans-serif;
    color: var(--ink);
  }
  .card {
    position: absolute;
    top: 184px;
    height: 491px;
    border-radius: 12px;
    box-sizing: border-box;
  }
  .card--front {
    left: 299px;
    width: 301px;
    background: var(--card-front);
  }
  .card--back {
    left: 645px;
    width: 305px;
    background: var(--card-back);
  }

  /* front */
  .company-name {
    position: absolute;
    left: 0;
    right: 0;
    top: 128px;
    margin: 0;
    text-align: center;
    font-size: 24px;
    font-weight: 600;
    line-height: 32px;
    letter-spacing: 0.06em;
    color: var(--ink);
  }
  .person {
    position: absolute;
    left: 0;
    right: 0;
    top: 283px;
    text-align: center;
  }
  .person__name {
    margin: 0;
    font-size: 19px;
    font-weight: 600;
    letter-spacing: 0.01em;
  }
  .person__role {
    margin: 6px 0 0;
    font-size: 13px;
    color: var(--ink-soft);
  }
  .contact {
    position: absolute;
    left: 0;
    right: 0;
    top: 361px;
    margin: 0;
    padding: 0;
    list-style: none;
    text-align: center;
    font-size: 16px;
    line-height: 22px;
  }

  /* back */
  .company-line {
    position: absolute;
    left: 0;
    right: 0;
    top: 165px;
    margin: 0;
    text-align: center;
    font-size: 17px;
    font-weight: 600;
    letter-spacing: 0.05em;
    color: var(--ink);
  }
  .member-badge {
    position: absolute;
    left: 97px;
    top: 251px;
    width: 112px;
    height: 78px;
    background: var(--ink);
    border-radius: 2px;
  }
  .registration-badge {
    position: absolute;
    left: 108px;
    top: 369px;
  }
</style>
</head>
<body>
  <section class="card card--front" aria-label="Business card front">
    <p class="company-name">RIDGE + STUDIO<br>LTD.</p>
    <div class="person">
      <h1 class="person__name">MARK DELFORD</h1>
      <p class="person__role">Architectural designer &amp; Design LBP</p>
    </div>
    <ul class="contact">
      <li>02 5163 2290</li>
      <li>mark@rplusd.co.nz</li>
      <li>www.rplusd.co.nz</li>
    </ul>
  </section>

  <section class="card card--back" aria-label="Business card back">
    <p class="company-line">RIDGE + STUDIO LTD.</p>
    <div class="member-badge" role="img" aria-label="Professional membership badge"></div>
    <svg class="registration-badge" width="90" height="90" viewBox="0 0 90 90" role="img" aria-label="Trade registration badge">
      <circle cx="45" cy="45" r="44" fill="var(--badge-grey)"/>
      <circle cx="45" cy="45" r="30" fill="var(--ink)"/>
    </svg>
  </section>
</body>
</html>
```